Business Card For Construction Company
Falcon Ridge Contractors
Business Card For Construction Company - Construction
Creative Brief
Professional
Tobias Varnell
No Address
TobiasVarnell@FalconRidgeCorp.example
www.FalconRidgeCorp.example

```html
<!DOCTYPE html>
<html lang="en">
<head>
<meta charset="utf-8">
<title>Falcon Ridge Contractors – Stationery</title>
<link rel="stylesheet" href="https://fonts.googleapis.com/css2?family=Russo+One&family=Open+Sans:wght@400;600&display=swap">
<style>
  :root {
    --bg: #eef0f3;
    --paper: #ffffff;
    --blue: #1f6fc0;
    --blue-dark: #0f4f96;
    --blue-light: #4a93dd;
    --ink: #2c3440;
    --muted: #7a8594;
    --faint: #e6edf5;
    --shadow: 0 3px 10px rgba(30, 40, 60, 0.16);
  }
  * { margin: 0; padding: 0; box-sizing: border-box; }
  html, body { width: 1200px; height: 936px; overflow: hidden; }
  body {
    background: var(--bg);
    font-family: "Open Sans", Arial, sans-serif;
    color: var(--ink);
    position: relative;
  }
  .sheet {
    position: absolute;
    background: var(--paper);
    box-shadow: var(--shadow);
    overflow: hidden;
  }
  .brand-name {
    font-family: "Russo One", Arial, sans-serif;
    color: var(--blue-dark);
    text-transform: uppercase;
    line-height: 1.05;
    letter-spacing: 0.02em;
  }
  .brand-mark {
    display: inline-block;
    background: var(--blue-dark);
  }
  .brand { display: flex; align-items: center; }

  /* Letterhead */
  .letterhead { left: 178px; top: 68px; width: 393px; height: 541px; }
  .letterhead .side-band {
    position: absolute; left: 20px; top: 0; bottom: 0; width: 12px;
    background: linear-gradient(90deg, var(--blue-dark), var(--blue-light));
  }
  .letterhead .brand { position: absolute; left: 22px; top: 22px; gap: 6px; }
  .letterhead .brand-mark { width: 18px; height: 18px; }
  .letterhead .brand-name { font-size: 10px; }
  .letterhead .contact {
    position: absolute; left: 240px; top: 22px;
    font-size: 5.5px; line-height: 1.55; color: var(--muted);
  }
  .letterhead .watermark {
    position: absolute; left: 110px; top: 250px; width: 120px; height: 100px;
    background: var(--faint);
  }

  /* Folder */
  .folder { left: 634px; top: 30px; width: 490px; height: 579px; }
  .folder .brand {
    position: absolute; left: 0; right: 0; top: 200px;
    flex-direction: column; gap: 14px;
  }
  .folder .brand-mark { width: 70px; height: 70px; }
  .folder .brand-name { font-size: 30px; text-align: center; }

  /* Business cards */
  .card { left: 43px; width: 198px; height: 106px; }
  .card-front { top: 660px; }
  .card-back { top: 786px; }
  .card-front .side-band {
    position: absolute; left: 12px; top: 0; bottom: 0; width: 8px;
    background: linear-gradient(90deg, var(--blue-dark), var(--blue-light));
  }
  .card-front .brand { position: absolute; left: 14px; top: 12px; gap: 4px; }
  .card-front .brand-mark { width: 12px; height: 12px; }
  .card-front .brand-name { font-size: 7px; }
  .card-front .details {
    position: absolute; left: 28px; top: 50px; font-size: 4.8px; line-height: 1.6; color: var(--muted);
  }
  .card-front .person {
    position: absolute; right: 12px; bottom: 12px; font-size: 5px; color: var(--muted); text-align: right;
  }
  .card-back .watermark {
    position: absolute; left: 20px; top: 16px; width: 80px; height: 70px; background: var(--faint);
  }
  .card-back .web {
    position: absolute; left: 20px; bottom: 8px; font-size: 4.5px; color: var(--muted);
  }

  /* Envelopes */
  .envelope { top: 665px; height: 215px; }
  .envelope-front { left: 261px; width: 437px; }
  .envelope-front .brand { position: absolute; left: 12px; top: 14px; gap: 5px; }
  .envelope-front .brand-mark { width: 15px; height: 15px; }
  .envelope-front .brand-name { font-size: 9px; }
  .envelope-back { left: 736px; width: 431px; }
  .envelope-back svg { position: absolute; left: 0; top: 0; }
  .envelope-back .web {
    position: absolute; left: 0; right: 0; top: 14px; text-align: center;
    color: #ffffff; font-size: 7px; letter-spacing: 0.25em;
  }
</style>
</head>
<body>

<section class="sheet letterhead">
  <div class="side-band"></div>
  <div class="brand"><span class="brand-mark"></span><span class="brand-name">Falcon Ridge<br>Contractors</span></div>
  <div class="contact">
    P: 555 010 2040<br>
    F: 555 010 2041<br>
    TobiasVarnell@FalconRidgeCorp.example<br>
    www.FalconRidgeCorp.example
  </div>
  <div class="watermark"></div>
</section>

<section class="sheet folder">
  <div class="brand"><span class="brand-mark"></span><span class="brand-name">Falcon Ridge<br>Contractors</span></div>
</section>

<section class="sheet card card-front">
  <div class="side-band"></div>
  <div class="brand"><span class="brand-mark"></span><span class="brand-name">Falcon Ridge<br>Contractors</span></div>
  <div class="details">
    P: 555 010 2040<br>
    M: 555 010 2042<br>
    TobiasVarnell@FalconRidgeCorp.example
  </div>
  <div class="person">Tobias Varnell<br>Project Manager</div>
</section>

<section class="sheet card card-back">
  <div class="watermark"></div>
  <div class="web">www.FalconRidgeCorp.example</div>
</section>

<section class="sheet envelope envelope-front">
  <div class="brand"><span class="brand-mark"></span><span class="brand-name">Falcon Ridge<br>Contractors</span></div>
</section>

<section class="sheet envelope envelope-back">
  <svg width="431" height="215" viewBox="0 0 431 215" aria-hidden="true">
    <defs>
      <linearGradient id="flap" x1="0" y1="0" x2="1" y2="0">
        <stop offset="0" stop-color="#0f4f96"/>
        <stop offset="0.5" stop-color="#2a7fd0"/>
        <stop offset="1" stop-color="#0f4f96"/>
      </linearGradient>
    </defs>
    <path d="M0 0 H431 V40 Q215 110 0 40 Z" fill="url(#flap)"/>
  </svg>
  <div class="web">www.FalconRidgeCorp.example</div>
</section>

</body>
</html>
```